Flat bootstrap design for existing site

I'm looking for a modern flat design based around an existing logo. This has to be a custom design (no external templates), and implemented into a bootstrap framework.

The logo is attached as 2 versions - choose whichever you want, that flows better with whatever design you choose.

Added screenshots of the existing site (currently using the default bootstrap layouts). Please make your designs around those pages in the screenshots (i.e. the homepage only has the postal code input and the header). The active page has 3 screenshots, because I wanted to illustrate the other states that would be visible (in the table rows).

This is a moving/junk removal website, just for some context.

Here's some example websites (flat designs) that I like, just to give you an idea of what I'm after.

https://www.plimvora.com/
https://dacklow.com/
https://trevanu.com/
https://quobrintal.com/en/

Coding

Coded - Design and coding required

Number of Pages Required

5+ page

Colors

Designer to choose colors to be used in the design.

Requirements
Must have
• It must be a modern/simple flat design, that is built around the existing logo (attached).
• It has to be implemented using bootstrap.

```html
<!DOCTYPE html>
<html lang="en">
<head>
<meta charset="utf-8">
<title>HAULVO – Junk Removal</title>
<link href="https://fonts.googleapis.com/css2?family=Lato:wght@400;700;900&display=swap" rel="stylesheet">
<style>
  :root {
    --sky: #38cdfd;
    --sky-light: #52d2f6;
    --page-bg: #f4f4f4;
    --white: #ffffff;
    --ink: #111111;
    --accent: #f26722;
    --placeholder: #9aa3c7;
  }
  * { box-sizing: border-box; margin: 0; padding: 0; }
  html, body {
    width: 1200px;
    height: 667px;
    overflow: hidden;
    background: var(--page-bg);
    font-family: "Lato", Arial, sans-serif;
  }
  .site-header {
    height: 89px;
    background: var(--sky);
    position: relative;
  }
  .brand {
    position: absolute;
    left: 78px;
    top: 0;
    width: 178px;
    height: 89px;
    background: var(--sky-light);
    display: flex;
    align-items: center;
    justify-content: center;
    color: var(--white);
    font-weight: 900;
    font-size: 30px;
    letter-spacing: 1px;
    text-decoration: none;
  }
  .main-nav {
    position: absolute;
    top: 31px;
    left: 599px;
    display: flex;
    align-items: center;
    list-style: none;
  }
  .main-nav a {
    display: block;
    color: var(--white);
    text-decoration: none;
    font-weight: 700;
    font-size: 15.5px;
    line-height: 27px;
    white-space: nowrap;
  }
  .nav-book {
    position: relative;
    border: 2px solid var(--white);
    padding: 0 10px;
    margin-right: 22px;
    height: 31px;
  }
  .nav-book a { line-height: 27px; }
  .nav-cursor {
    position: absolute;
    left: 59px;
    top: 16px;
  }
  .nav-how { margin-right: 33px; }
  .nav-driver { margin-right: 37px; }

  .hero {
    text-align: center;
    padding-top: 124px;
  }
  .hero-title {
    display: flex;
    justify-content: center;
    align-items: center;
    color: var(--sky);
    font-weight: 700;
    font-size: 57px;
    letter-spacing: 0.5px;
    height: 112px;
  }
  .hero-tag {
    display: inline-block;
    background: var(--ink);
    color: var(--white);
    font-weight: 400;
    padding: 8px 16px 6px;
    margin: 0 10px;
    line-height: 1;
    transform: rotate(-12deg);
  }
  .booking-form {
    display: flex;
    justify-content: center;
    gap: 6px;
    margin-top: 48px;
  }
  .postal-input {
    width: 251px;
    height: 44px;
    border: 2px solid var(--sky);
    border-radius: 3px;
    background: var(--white);
    padding: 0 14px;
    font-family: "Lato", Arial, sans-serif;
    font-size: 15px;
    color: var(--ink);
  }
  .postal-input::placeholder { color: var(--placeholder); }
  .book-button {
    width: 134px;
    height: 44px;
    border: 2px solid var(--sky);
    border-radius: 3px;
    background: var(--accent);
    color: var(--white);
    font-family: "Lato", Arial, sans-serif;
    font-weight: 700;
    font-size: 15.5px;
  }
</style>
</head>
<body>
  <header class="site-header">
    <a class="brand" href="#">HAULVO</a>
    <ul class="main-nav">
      <li class="nav-book">
        <a href="#">BOOK</a>
        <svg class="nav-cursor" width="24" height="24" viewBox="0 0 24 24" aria-hidden="true">
          <path d="M1 1 L22 10 L12 12 L10 22 Z" fill="var(--white)"/>
        </svg>
      </li>
      <li class="nav-how"><a href="#">HOW IT WORKS</a></li>
      <li class="nav-driver"><a href="#">BECOME A DRIVER</a></li>
      <li><a href="#">SIGN IN</a></li>
    </ul>
  </header>

  <main class="hero">
    <h1 class="hero-title">
      <span>NEED A</span>
      <span class="hero-tag">JUNK</span>
      <span>REMOVED?</span>
    </h1>
    <form class="booking-form">
      <input class="postal-input" type="text" placeholder="Enter your postal code here">
      <button class="book-button" type="button">BOOK NOW!</button>
    </form>
  </main>
</body>
</html>
```